We need a designer to help us represent our unique approach to creating lesson plans for digital learning. At the Coastal Workshop for Media Fluency, held in Providence RI this July 13 - 18, we'll use your design with 100 teachers and then put it online to reach hundreds of thousands more.

We have a draft visual of our model that we like - but it's not pretty (Since we are not designers, it looks a little clunky).

Please create a simple and attractive design in two versions: (1) one that we can use as a 1-page printed handout and (2) one that we can use where teachers can fill in sections and write ideas under each section of the graphic.

Why you should bid on this job? We're a leading provider of digital and media literacy curriculum resources with a huge international and national audience. Working with us will establish your expertise in the area of educational multimedia design.

Target Market(s)

Elementary and secondary teachers in public schools

Industry/Entity Type

Digital

Font styles to use
Sans Serif

Requirements
Must have
• TITLE : Digital Literacy Curriculum Framework

1 page version - suitable for use as a poster or 1-page flyer

Fillable form version - suitable for use as a handout with spaces for teachers to write

```html
<!DOCTYPE html>
<html lang="en">
<head>
<meta charset="utf-8">
<title>Digital Literacy Curriculum Framework</title>
<link rel="stylesheet" href="https://fonts.googleapis.com/css2?family=Open+Sans:wght@400;600&family=Didact+Gothic&family=Encode+Sans+Semi+Condensed:wght@300;400;600&display=swap">
<style>
  :root {
    --ink: #111111;
    --ink-soft: #3a3a3a;
    --bg-light: #ffffff;
    --bg-dark: #7f7f7f;
    --green: #22b573;
    --green-deep: #0e7a48;
    --orange: #f2b01e;
    --orange-deep: #b97a05;
    --purple: #7a2fbf;
    --purple-deep: #4e1585;
    --pink: #e0195c;
    --pink-deep: #9e0b3c;
    --blue: #1f8fe6;
    --blue-deep: #0b5cb0;
    --label-shadow: rgba(0,0,0,0.75);
  }
  html, body {
    margin: 0;
    padding: 0;
    overflow: hidden;
  }
  .framework {
    position: relative;
    width: 1200px;
    height: 1000px;
    overflow: hidden;
    background:
      radial-gradient(ellipse 420px 360px at 620px 470px, rgba(255,255,255,0.9), rgba(255,255,255,0) 70%),
      linear-gradient(105deg, var(--bg-light) 0%, #e4e4e4 35%, #a9a9a9 70%, var(--bg-dark) 100%);
    font-family: "Didact Gothic", "Open Sans", sans-serif;
    color: var(--ink);
  }
  .framework-title {
    position: absolute;
    left: 0;
    right: 0;
    top: 22px;
    margin: 0;
    text-align: center;
    font-family: "Open Sans", sans-serif;
    font-weight: 600;
    font-size: 30px;
    line-height: 1;
    color: var(--ink);
    z-index: 2;
  }
  .corner {
    position: absolute;
    margin: 0;
    font-family: "Open Sans", sans-serif;
    font-weight: 400;
    font-size: 36px;
    line-height: 1;
  }
  .corner--purpose { left: 24px; top: 28px; }
  .corner--assessment { right: 28px; top: 28px; }
  .corner--content { left: 24px; bottom: 52px; font-size: 42px; }
  .corner--pedagogy { right: 26px; bottom: 56px; font-size: 38px; }

  .splash {
    position: absolute;
    filter: blur(2px);
  }
  .splash--standards {
    left: 120px; top: 78px; width: 520px; height: 292px;
    border-radius: 48% 52% 40% 60% / 55% 45% 55% 45%;
    background: radial-gradient(ellipse at 55% 55%, #5fd49a 0%, var(--green) 45%, var(--green-deep) 100%);
    transform: rotate(-6deg);
  }
  .splash--work {
    left: 660px; top: 120px; width: 390px; height: 230px;
    border-radius: 55% 45% 50% 50% / 50% 60% 40% 50%;
    background: radial-gradient(ellipse at 45% 45%, #ffd36a 0%, var(--orange) 50%, var(--orange-deep) 100%);
  }
  .splash--texts {
    left: 130px; top: 340px; width: 360px; height: 250px;
    border-radius: 45% 55% 50% 50% / 55% 45% 55% 45%;
    background: radial-gradient(ellipse at 70% 45%, #e6c9ff 0%, #a45fe0 30%, var(--purple) 60%, var(--purple-deep) 100%);
  }
  .splash--strategies {
    left: 300px; top: 570px; width: 320px; height: 420px;
    border-radius: 50% 50% 45% 55% / 35% 35% 65% 65%;
    background: radial-gradient(ellipse at 55% 20%, #ffe1ea 0%, #f06a96 25%, var(--pink) 55%, var(--pink-deep) 100%);
  }
  .splash--tools {
    left: 680px; top: 320px; width: 360px; height: 670px;
    border-radius: 40% 60% 35% 65% / 30% 40% 60% 70%;
    background: radial-gradient(ellipse at 20% 30%, #e8f6ff 0%, #6cc3f5 25%, var(--blue) 55%, var(--blue-deep) 100%);
  }
  .core-glow {
    position: absolute;
    left: 400px; top: 290px; width: 440px; height: 360px;
    border-radius: 50%;
    background: radial-gradient(ellipse at center, #ffffff 0%, rgba(255,255,255,0.95) 45%, rgba(255,255,255,0) 72%);
  }

  .label {
    position: absolute;
    margin: 0;
    font-family: "Encode Sans Semi Condensed", sans-serif;
    font-weight: 400;
    line-height: 0.95;
    text-align: center;
    text-shadow: 0 0 1px var(--label-shadow), 1px 2px 3px var(--label-shadow);
  }
  .label--standards { left: 256px; top: 238px; font-size: 60px; color: #4fd08d; }
  .label--work { left: 716px; top: 190px; font-size: 44px; color: #ffd56b; }
  .label--texts { left: 254px; top: 420px; font-size: 60px; color: #c48af0; }
  .label--strategies { left: 380px; top: 626px; font-size: 42px; color: #f7c4d4; }
  .label--tools { left: 788px; top: 606px; font-size: 90px; font-weight: 300; color: #d8eefc; }

  .core {
    position: absolute;
    margin: 0;
    line-height: 1;
    white-space: nowrap;
  }
  .core--learners { left: 554px; top: 352px; font-size: 38px; }
  .core--task { left: 540px; top: 406px; font-size: 60px; color: var(--ink-soft); }
  .core--activity { left: 546px; top: 474px; font-size: 54px; font-family: "Open Sans", sans-serif; font-weight: 600; letter-spacing: -1px; }
  .core--context { left: 548px; top: 552px; font-size: 42px; }
  .core--self {
    left: 430px; top: 430px; font-size: 50px;
    transform: rotate(-90deg); transform-origin: center;
  }
  .core--community {
    left: 688px; top: 461px; font-size: 36px;
    transform: rotate(-90deg); transform-origin: center;
  }
</style>
</head>
<body>
<main class="framework" aria-label="Digital Literacy Curriculum Framework">
  <h1 class="framework-title">Digital Literacy Curriculum Framework</h1>

  <p class="corner corner--purpose">Purpose</p>
  <p class="corner corner--assessment">Assessment</p>
  <p class="corner corner--content">Content</p>
  <p class="corner corner--pedagogy">Pedagogy</p>

  <div class="splash splash--standards" role="img" aria-label="Green paint splash behind Standards"></div>
  <div class="splash splash--work" role="img" aria-label="Orange paint splash behind Work product"></div>
  <div class="splash splash--texts" role="img" aria-label="Purple paint splash behind Texts"></div>
  <div class="splash splash--strategies" role="img" aria-label="Magenta paint splash behind Instructional strategies"></div>
  <div class="splash splash--tools" role="img" aria-label="Blue paint splash behind Tools"></div>
  <div class="core-glow"></div>

  <p class="label label--standards">Standards</p>
  <p class="label label--work">Work<br>product</p>
  <p class="label label--texts">Texts</p>
  <p class="label label--strategies">Instructional<br>strategies</p>
  <p class="label label--tools">Tools</p>

  <p class="core core--learners">Learners</p>
  <p class="core core--task">Task or</p>
  <p class="core core--activity">activity</p>
  <p class="core core--context">Context</p>
  <p class="core core--self">Self</p>
  <p class="core core--community">Community</p>
</main>
</body>
</html>
```